Bright Towns Forum PowerPoint Design Template and Sample Deck

The Bright Towns Forum is an international organization that seeks to improve the livability, workability and sustainability of the world’s cities.
We seek a versatile PowerPoint design template with 10 slide types plus a “self-documenting” sample deck. Your design will be used in keynote speeches and workshops around the world.
After the contest is completed, we will ask the winning designer to add 10-20 additional slide types for $75 per slide. We also seek a long-term relationship whereby we can request “custom” slides and/or ask the designer to touch up the slides we build to make them better.
FILES. We have uploaded several files:
2. PALETTE. Shows our official colors.
3 LOGOS. Several individual files with different variations of our logo. Some with our motto, some without.
2. SAMPLE SLIDES. Because we were unable to successfully upload our sample deck, we are making it available via this FileNook link:
https://www.filenook-example.com/s/k7qrtmzp2wd9hxa/The%20Bright%20Towns%20Forum%20Design%20Contest%20Notes.docx?dl=0
Target Market(s)
Mayors, department heads, CIOs, senior executives from technology companies
Industry/Entity Type
Information Technology
Colors
Designer to choose colors to be used in the design.
Requirements
Must have
- Please see uploaded Word document for requirements, nice to haves and should not haves and uploaded palette for color preferences.
Nice to have
- see above
Should not have
- see above

```html
<!DOCTYPE html>
<html lang="en">
<head>
<meta charset="utf-8">
<title>Bright Towns Forum – Five Step Overview</title>
<link href="https://fonts.googleapis.com/css2?family=Open+Sans:wght@400;600;700&display=swap" rel="stylesheet">
<style>
  :root {
    --navy: #00448a;
    --navy-deep: #0d3766;
    --white: #ffffff;
    --rule: rgba(255, 255, 255, 0.75);
    --bg-top: #56606c;
    --bg-mid: #434b57;
    --bg-low: #2f3744;
    --bubble: rgba(255, 255, 255, 0.08);
  }
  * { box-sizing: border-box; margin: 0; padding: 0; }
  html, body { width: 1200px; height: 675px; overflow: hidden; }
  body { font-family: "Open Sans", Arial, sans-serif; color: var(--white); background: var(--bg-low); }

  .slide { position: relative; width: 1200px; height: 675px; overflow: hidden; }

  .slide-backdrop {
    position: absolute; inset: 0;
    background:
      radial-gradient(ellipse at 40% 25%, #7a7f86 0%, rgba(122,127,134,0) 45%),
      radial-gradient(ellipse at 78% 30%, #6f6a66 0%, rgba(111,106,102,0) 40%),
      linear-gradient(160deg, var(--bg-top) 0%, var(--bg-mid) 50%, var(--bg-low) 100%);
  }
  .backdrop-bubbles { position: absolute; inset: 0; }

  .slide-title {
    position: absolute; left: 60px; top: 56px;
    font-size: 45px; font-weight: 400; letter-spacing: 0.2px; line-height: 1.1;
  }

  .step { position: absolute; top: 185px; width: 180px; text-align: center; }
  .step-badge {
    width: 132px; height: 132px; margin: 0 auto;
    border-radius: 50%; background: var(--white);
    display: flex; align-items: center; justify-content: center;
    box-shadow: 3px 5px 4px rgba(0,0,0,0.45);
  }
  .step-badge-inner {
    width: 117px; height: 117px; border-radius: 50%; background: var(--navy);
    display: flex; align-items: center; justify-content: center;
  }
  .step-badge svg { width: 62px; height: 62px; fill: none; stroke: var(--white); stroke-width: 2.2; stroke-linecap: round; stroke-linejoin: round; }
  .step-heading {
    margin-top: 38px; padding-bottom: 10px;
    font-size: 21px; font-weight: 700;
    border-bottom: 1px solid var(--rule);
  }
  .step-text { margin-top: 18px; font-size: 17px; line-height: 24px; }

  .page-number {
    position: absolute; left: 1089px; top: 622px;
    width: 50px; height: 50px; border-radius: 50%;
    background: var(--navy-deep);
    display: flex; align-items: center; justify-content: center;
    font-size: 14px;
  }
</style>
</head>
<body>
<main class="slide">
  <div class="slide-backdrop" role="img" aria-label="Photo of two business colleagues looking at a tablet together, dimmed behind the content"></div>
  <svg class="backdrop-bubbles" viewBox="0 0 1200 675" aria-hidden="true">
    <path d="M560 0 C420 40 400 220 480 300 L470 330 L520 300 C620 340 760 320 820 220 C860 140 820 40 760 0 Z" fill="var(--bubble)"/>
    <path d="M700 230 C700 130 840 80 980 80 C1120 80 1200 160 1200 230 C1200 320 1120 380 1060 400 L1080 440 L1010 405 C860 420 700 340 700 230 Z" fill="var(--bubble)"/>
  </svg>

  <h1 class="slide-title">Lorem Ipsum is simply dummy</h1>

  <section class="step" style="left:63px">
    <div class="step-badge"><div class="step-badge-inner">
      <svg viewBox="0 0 64 64" aria-hidden="true">
        <path d="M14 10 h30 v44 h-30 z"/><path d="M10 14 a4 4 0 0 1 8 0 M44 10 a4 4 0 0 1 4 4"/>
        <path d="M19 22 l2 2 4-4 M28 22 h10 M19 32 l2 2 4-4 M28 32 h10 M19 42 l2 2 4-4 M28 42 h10"/>
        <path d="M50 18 h6 v34 l-3 6 -3-6 z M50 24 h6"/>
      </svg>
    </div></div>
    <h2 class="step-heading">Lorem Ipsum</h2>
    <p class="step-text">Lorem Ipsum is simply dummy text of the printing and typesetting industry.</p>
  </section>

  <section class="step" style="left:287px">
    <div class="step-badge"><div class="step-badge-inner">
      <svg viewBox="0 0 64 64" aria-hidden="true">
        <path d="M12 28 a20 20 0 0 0 26 22 z" fill="var(--white)"/>
        <path d="M25 39 l10-12"/><circle cx="36" cy="26" r="2" fill="var(--white)"/>
        <path d="M40 18 a8 8 0 0 1 6 6 M42 12 a14 14 0 0 1 10 10"/>
      </svg>
    </div></div>
    <h2 class="step-heading">Lorem Ipsum</h2>
    <p class="step-text">Lorem Ipsum is simply dummy text of the printing and typesetting industry.</p>
  </section>

  <section class="step" style="left:515px">
    <div class="step-badge"><div class="step-badge-inner">
      <svg viewBox="0 0 64 64" aria-hidden="true">
        <circle cx="26" cy="26" r="13"/><path d="M35 35 l15 15"/>
      </svg>
    </div></div>
    <h2 class="step-heading">Lorem Ipsum</h2>
    <p class="step-text">Lorem Ipsum is simply dummy text of the printing and typesetting industry.</p>
  </section>

  <section class="step" style="left:743px">
    <div class="step-badge"><div class="step-badge-inner">
      <svg viewBox="0 0 64 64" aria-hidden="true">
        <circle cx="26" cy="38" r="12" stroke-dasharray="5 3.4"/><circle cx="26" cy="38" r="5"/>
        <circle cx="46" cy="18" r="8" stroke-dasharray="3.5 2.8"/><circle cx="46" cy="18" r="3"/>
      </svg>
    </div></div>
    <h2 class="step-heading">Lorem Ipsum</h2>
    <p class="step-text">Lorem Ipsum is simply dummy text of the printing and typesetting industry.</p>
  </section>

  <section class="step" style="left:967px">
    <div class="step-badge"><div class="step-badge-inner">
      <svg viewBox="0 0 64 64" aria-hidden="true">
        <circle cx="32" cy="32" r="3"/>
        <path d="M14 30 a18 18 0 0 1 30-12 M50 34 a18 18 0 0 1-30 12"/>
        <path d="M10 26 l4 5 4-5 M54 38 l-4-5 -4 5"/>
      </svg>
    </div></div>
    <h2 class="step-heading">Lorem Ipsum</h2>
    <p class="step-text">Lorem Ipsum is simply dummy text of the printing and typesetting industry.</p>
  </section>

  <div class="page-number">11</div>
</main>
</body>
</html>
```